Elegant and modern Wedding Photography brochure

My existing brochure (attached) needs a major facelift. This is one of the main selling tools - it gets emailed to my clients when they make an equiry on what packages i offer and it is printed out and walked through at our first meeting. This brochure is as critical as my website - it needs to sing!

I'm looking for an eye-catching design that says:
Elegant
Modern
Clean
Crisp
Not cutesy or lovey-dovey thanks - we are more sophisticated and professional than that.

Update images to some of the latest weddings I've shot also. Let me know files and resolution you need. I've enabled right-click to download images on my site for a limited time. Please note that I retain copyright and will pursue any breeches.

Http://www.sarahkelbrin.com/Melbourne-wedding-photography
Updates

Thanks for all of your designs! Will take a few days to decide.

Target Market(s)

Australian Women aged 24-44

Industry/Entity Type

Wedding

Font styles to use
Other font styles liked:
• Century Gothic

Requirements
Must have
• Easy to print - does not have to be 6 A4 pages like the existing brochure
Nice to have
• Some full page images - The photos are supposed to be the hero here :-)
Should not have
• Not cutesy or lovey-dovey thanks - we are more sophisticated and professional than that.

No black backgrounds, I prefer a white thanks

No images in organic shaped boxes (like the rectangles in the logo - no thanks).
Keep the lines straight and sharp

```html
<!DOCTYPE html>
<html lang="en">
<head>
<meta charset="utf-8">
<title>Sarah Kelbrin Wedding Photography</title>
<link href="https://fonts.googleapis.com/css2?family=Didact+Gothic&display=swap" rel="stylesheet">
<style>
  :root {
    --plum: #8e2a8b;
    --frame-grey: #8c8c8f;
    --ink: #111111;
    --muted: #8a8a8a;
    --paper: #ffffff;
  }
  * { margin: 0; padding: 0; box-sizing: border-box; }
  html, body { width: 853px; height: 1200px; overflow: hidden; background: var(--paper); }
  .flyer {
    position: relative;
    width: 853px;
    height: 1200px;
    font-family: "Didact Gothic", "Century Gothic", sans-serif;
    color: var(--ink);
  }
  .gallery { position: absolute; left: 0; top: 0; }
  .headline {
    position: absolute;
    left: 96px;
    top: 654px;
    font-size: 49px;
    font-weight: 400;
    line-height: 52px;
    color: var(--plum);
    white-space: nowrap;
  }
  .body-copy {
    position: absolute;
    left: 97px;
    top: 793px;
    width: 700px;
    font-size: 18.5px;
    line-height: 21.5px;
    white-space: nowrap;
  }
  .body-copy p + p { margin-top: 21px; }
  .brand {
    position: absolute;
    left: 476px;
    top: 1044px;
    display: flex;
    align-items: center;
    gap: 14px;
  }
  .brand-mark { width: 46px; height: 46px; background: var(--plum); }
  .brand-name { font-size: 34px; color: var(--plum); }
  .contact {
    position: absolute;
    left: 0;
    top: 1101px;
    width: 853px;
    text-align: center;
    color: var(--muted);
    white-space: nowrap;
  }
  .contact-line { font-size: 18.5px; }
  .contact-line .sep { margin: 0 5px; }
  .contact-address { font-size: 14px; margin-top: 1px; }
</style>
</head>
<body>
<div class="flyer">
  <svg class="gallery" width="853" height="640" viewBox="0 0 853 640">
    <defs>
      <linearGradient id="tone-street" x1="0" y1="0" x2="1" y2="1">
        <stop offset="0" stop-color="#6d6f73"/><stop offset="1" stop-color="#2f3034"/>
      </linearGradient>
      <linearGradient id="tone-park" x1="0" y1="0" x2="1" y2="1">
        <stop offset="0" stop-color="#8d9a7c"/><stop offset="1" stop-color="#4d5546"/>
      </linearGradient>
      <linearGradient id="tone-veil" x1="0" y1="0" x2="1" y2="1">
        <stop offset="0" stop-color="#d8d8d8"/><stop offset="1" stop-color="#7a7a7a"/>
      </linearGradient>
      <linearGradient id="tone-groomsmen" x1="0" y1="0" x2="0" y2="1">
        <stop offset="0" stop-color="#a9a9a9"/><stop offset="1" stop-color="#3a3a3a"/>
      </linearGradient>
      <linearGradient id="tone-garden" x1="0" y1="0" x2="0" y2="1">
        <stop offset="0" stop-color="#b9d68a"/><stop offset="1" stop-color="#4b4a62"/>
      </linearGradient>
    </defs>

    <g class="photo-frame" role="img" aria-label="Couple posing in front of a graffiti wall">
      <rect x="206" y="114" width="280" height="214" fill="url(#tone-street)" stroke="var(--plum)" stroke-width="5"/>
    </g>
    <g class="photo-frame" role="img" aria-label="Black and white portrait of a bride in a veil">
      <rect x="162" y="334" width="184" height="142" fill="url(#tone-veil)" stroke="var(--plum)" stroke-width="5"/>
    </g>
    <g class="photo-frame" role="img" aria-label="Bride and groom standing among trees">
      <rect x="388" y="258" width="288" height="206" fill="url(#tone-park)" stroke="var(--frame-grey)" stroke-width="5"/>
    </g>
    <g class="photo-frame" role="img" aria-label="Black and white photo of groomsmen in suits">
      <rect x="282" y="428" width="186" height="150" fill="url(#tone-groomsmen)" stroke="var(--frame-grey)" stroke-width="5"/>
    </g>
    <g class="photo-frame" role="img" aria-label="Bridesmaids holding bouquets in a garden">
      <rect x="486" y="444" width="218" height="174" fill="url(#tone-garden)" stroke="var(--plum)" stroke-width="5"/>
    </g>
  </svg>

  <h1 class="headline">How do you want to remember<br>your special day?</h1>

  <div class="body-copy">
    <p>Elegant, stunning, fuss-free photography that doesn’t cost the earth will capture<br>those memories for a lifetime!</p>
    <p>Wedding photography packages start from $1650 and are fully inclusive of<br>fun-filled creative &amp; journalistic coverage, digital negatives and professionally<br>edited album.</p>
    <p>Contact Sarah today to arrange an informal catch-up, discuss your requirements<br>and find out more about the early booking bonus!</p>
  </div>

  <div class="brand">
    <span class="brand-mark"></span>
    <span class="brand-name">Sarah Kelbrin</span>
  </div>

  <div class="contact">
    <p class="contact-line">www.sarahkelbrin.com<span class="sep">|</span>Mobile: 0412 555 208<span class="sep">|</span>Email: sarah@sarahkelbrin.com</p>
    <p class="contact-address">Hollis Lane, Seddon, VIC, 3011</p>
  </div>
</div>
</body>
</html>
```